​Silver Harbor Rhythm provides personal, friendly service in a fun and high energy environment. We are based in Vermont.

We would like a card that appeals to a wide range of audiences as we do a wide range of events. Please feel free to check out our website silverharborrhythm.net for inspiration.

Target Market(s)

weddings, corporate, birthday parties, colleges

Industry/Entity Type

Business

Contact Information for Business Card

Silver Harbor Rhythm
Providing Entertainment For All Occasions
555 274 9160
silverharborrhythm@mailnest.net
silverharborrhythm.net

```html
<!DOCTYPE html>
<html lang="en">
<head>
<meta charset="utf-8">
<title>Silver Harbor Rhythm – Business Card</title>
<link rel="stylesheet" href="https://fonts.googleapis.com/css2?family=Source+Sans+3:wght@400;600;700&display=swap">
<style>
  :root {
    --canvas: #e9e6e1;
    --forest: #2f5a12;
    --forest-dark: #244a0c;
    --paper: #ffffff;
    --ink: #3c3c3c;
    --ink-soft: #6a6a6a;
    --rule: #c9c9c9;
    --night: #140405;
    --snow: #f4f4f4;
  }
  * { margin: 0; padding: 0; box-sizing: border-box; }
  html, body {
    width: 1200px; height: 829px; overflow: hidden;
    background: var(--canvas);
    font-family: "Source Sans 3", Arial, sans-serif;
  }
  .stage {
    width: 1200px; height: 829px;
    display: flex; align-items: center; justify-content: center; gap: 40px;
  }
  .card {
    position: relative;
    width: 540px; height: 309px;
    overflow: hidden;
    box-shadow: 0 6px 18px rgba(0,0,0,.18);
  }

  /* Front */
  .card--front { background: var(--paper); }
  .front__band {
    position: absolute; left: 0; top: 0; width: 100%; height: 74px;
    background: var(--forest);
  }
  .front__rule {
    position: absolute; left: 0; top: 80px; width: 100%; height: 2px;
    background: var(--forest);
  }
  .front__brand {
    position: absolute; left: 120px; top: 96px;
    display: flex; align-items: center; gap: 8px;
  }
  .front__brand-mark {
    width: 12px; height: 12px; background: var(--forest);
  }
  .front__brand-name {
    font-size: 22px; font-weight: 700; color: var(--forest);
    letter-spacing: .5px; text-transform: uppercase;
  }
  .front__person {
    position: absolute; right: 300px; top: 170px;
    text-align: right; color: var(--ink);
  }
  .front__name { font-size: 19px; font-weight: 700; color: var(--forest); line-height: 1.1; }
  .front__title { font-size: 14px; color: var(--ink-soft); margin-bottom: 10px; }
  .front__address { font-size: 13.5px; line-height: 1.3; color: var(--ink-soft); }
  .front__divider {
    position: absolute; left: 258px; top: 140px; width: 1px; height: 130px;
    background: var(--rule);
  }
  .front__contacts {
    position: absolute; left: 274px; top: 150px;
    list-style: none; font-size: 13px; color: var(--ink);
  }
  .front__contacts li { display: flex; align-items: center; gap: 7px; margin-bottom: 7px; }
  .front__contacts svg { width: 13px; height: 13px; flex: none; }

  /* Back */
  .card--back { background: var(--night); }
  .back__brand {
    position: absolute; left: 0; right: 0; top: 108px;
    display: flex; justify-content: center; align-items: center; gap: 12px;
  }
  .back__brand-mark { width: 18px; height: 18px; background: var(--snow); }
  .back__brand-name {
    font-size: 34px; font-weight: 700; color: var(--snow);
    text-transform: uppercase; letter-spacing: 1px;
  }
  .back__url {
    position: absolute; right: 30px; bottom: 26px;
    font-size: 17px; color: var(--snow); letter-spacing: 1.5px;
  }
</style>
</head>
<body>
<main class="stage">
  <section class="card card--front" aria-label="Business card front">
    <div class="front__band"></div>
    <div class="front__rule"></div>
    <div class="front__brand">
      <span class="front__brand-mark"></span>
      <span class="front__brand-name">Silver Harbor Rhythm</span>
    </div>
    <div class="front__person">
      <p class="front__name">Your Name</p>
      <p class="front__title">Title</p>
      <p class="front__address">Sreet Name, City Name<br>Zip Code-00000</p>
    </div>
    <div class="front__divider"></div>
    <ul class="front__contacts">
      <li>
        <svg viewBox="0 0 16 16" aria-hidden="true"><circle cx="8" cy="8" r="8" fill="#2f5a12"/><path d="M5 4.5l1.6-.5 1 2-1 .8a5 5 0 0 0 2.6 2.6l.8-1 2 1-.5 1.6c-3.5.3-6.8-3-6.5-6.5z" fill="#fff"/></svg>
        555 274 9160
      </li>
      <li>
        <svg viewBox="0 0 16 16" aria-hidden="true"><circle cx="8" cy="8" r="8" fill="#2f5a12"/><rect x="4" y="5.2" width="8" height="5.6" fill="#fff"/><path d="M4 5.2l4 3 4-3" stroke="#2f5a12" stroke-width="1" fill="none"/></svg>
        silverharborrhythm@mailnest.net
      </li>
      <li>
        <svg viewBox="0 0 16 16" aria-hidden="true"><circle cx="8" cy="8" r="8" fill="#2f5a12"/><circle cx="8" cy="8" r="4.2" stroke="#fff" stroke-width="1" fill="none"/><ellipse cx="8" cy="8" rx="1.8" ry="4.2" stroke="#fff" stroke-width="1" fill="none"/><path d="M3.8 8h8.4" stroke="#fff" stroke-width="1"/></svg>
        www.silverharborrhythm.net
      </li>
    </ul>
  </section>

  <section class="card card--back" aria-label="Business card back">
    <div class="back__brand">
      <span class="back__brand-mark"></span>
      <span class="back__brand-name">Silver Harbor Rhythm</span>
    </div>
    <p class="back__url">www.silverharborrhythm.net</p>
  </section>
</main>
</body>
</html>
```